Velvet Ladle Wishes Website Design; Cupcake Business with a unique and bespoke design element

We need a website design for a new bespoke and unique business making gourmet cupcakes - but MOST IMPORTANTLY we design and handmake cupcake wrappers and toppers specifically for each client's event. We are based in Sydney, Australia. The final resulting website should be elegant yet whimsical reflecting the notion of dreams and very elegant events eg weddings and very special parties.

We want to eventually have about 5 pages, HOWEVER, this project is specifically for the first page (ie Home page) and one other only. The final required pages are: a HOME page; ABOUT US page; PHOTO GALLERY page; FLAVOUR MENU & OTHER PRODUCTS page; CONTACT & INTERNET ENQUIRY page.

We expect the HOME page to be quite elaborate, perhaps including some animation. We will be providing the text content for all the other pages, and basically they will have the same background as the home page. We are looking for a clean design that runs across each page thus giving the website a continuity that pulls it all together. We would like our logo to be included on each page.

PLEASE NOTE: We will want multiple pages worked on in the handover phase but initially we want a very concise, consistent template to limit the amount of work to prospective designers.

While we are primarily looking for the design phase to be covered by this project, we would certainly appreciate coding to be included and will take that into consideration when choosing a winner.
Updates

Hi Designers

We have added some more information to our brief - please review it.

Thanks and happy designing

Hi Designers

Please note that we have increased our Prize money to $750.00.  We hope this encourages you to participate.

Thanks and regards
Velvet Ladle Wishes

Hi Designers

We've just posted some photos to help give you an idea of what we do.  Please note our attention to detail and precision in our work.

Thanks
Velvet Ladle Wishes

Hi Designers

Please Note:  What makes us different  to any other cupcake business is that we design cupcake wrappers and toppers, unique to our client's event whether it be a wedding, a birthday party or product launch.  We consult with our client to understand themes, colours, styles etc.  We then have our designs printed, next they are cut by a specialised computerised cutting machine,  We assemble everything by hand, and usually embellish the wrapper and topper with pearls, crystals, feathers, lace, ribbons or whatever else is appropriate for the event.  All work is totally bespoke, unique and individual.  No other cupcake supplier that we know of goes to these lengths to satisfy their client's dreams.

THE WRAPPER AND TOPPER IS OUR PRIMARY SELLING POINT. 

PLEASE NOTE:- We have uploaded a new photograph which we want to be used as the main photograph on the landing page.

We have removed all previous photographs of cupcakes (except for one that we can't get rid of).

We don't want a picture of a cupcake on the landing page we want the image _D7C3239.jpg to be used for that purpose.

We have also uploaded our logo in a number of file formats as we have had requests from you for these.

Hi designers

we have a crazy busy weekend on and won't be able to make any decisions re our competition until Monday  -  sorry to keep you in suspense, just a couple more days please!

regards
Pam

Target Market(s)

Primarily women - brides, new mothers (Christenings), Event Planners, who place an emphasis on the beauty of a product rather than the cost

Industry/Entity Type

Events

Requirements
Must have
• It must have our Logo (see attached upload) on each page (our logo is a butterfly atop a cupcake resting on a spoon and our motto is "Creating Delicious Works of Art". The colours used are pale pink, blue and chocolate brown and we'd expect these colours to be repeated in the final website.
The website must have a photo gallery which we can access and add to/change as our business grows.
We need a contact page which has an "internet enquiry form".
There should be a "Menu" page describing our cupcake flavours.
The Home page must have a party/event feel to it - definitely making an enquirer want to enter further into the site.
Nice to have
• Our logo is attached below in the "uploads". One idea that we have had is to use the butterfly in the logo but start it as a caterpillar crawling on the screen; as it spins it's cocoon the words "Sweet Dreams Little Caterpillar" would appear on screen; this would incorporate the "Dreams" in our Business Name; then our logo butterfly would hatch. This encapsulates the idea of taking something plain (caterpillar/cupcake) and creating something beautiful (butterfly/OUR cupcake).
However, we are open to other design ideas.
The colours we would like to have are pale pink, blue and chocolate brown in the design.

Some websites we really admire are: www.mirabellhart.com www.ribbonglitterloaf.com.au and www.greetingsoriel.com.au
These websites have a lightness and sense of fantasy to them. They do not convey a corporate image at all, rather they make you want to be at the party.
Should not have
• No "Corporate" style.

Most Important: We already have a website which we are not happy with - that is why we are going through this exercise to replace it. That means we DO NOT want anything along the lines of our current website. We are expecting some fresh ideas for our prize money.

```html
<!DOCTYPE html>
<html lang="en">
<head>
<meta charset="utf-8">
<title>Velvet Ladle Wishes</title>
<link href="https://fonts.googleapis.com/css2?family=Fondamento&family=Nunito+Sans:wght@400;600&family=Arimo&display=swap" rel="stylesheet">
<style>
:root{
  --page-pink:#f5c8cf;
  --sheet:#fbdde0;
  --brown-dark:#4d2a2f;
  --brown:#5f363c;
  --brown-mid:#6e454b;
  --text-brown:#4a2c22;
  --magenta:#e0196f;
  --blue-head:#2f6a95;
  --feature-pink:#f9a7ab;
  --standard-blue:#68a0c9;
  --white:#ffffff;
}
*{margin:0;padding:0;box-sizing:border-box}
html,body{width:1200px;height:1025px;overflow:hidden}
body{background:var(--page-pink);font-family:"Nunito Sans",sans-serif;position:relative;color:var(--text-brown)}
.sheet{position:absolute;left:155px;top:0;width:890px;height:1025px;background:var(--sheet);box-shadow:0 0 10px rgba(120,60,70,.25)}
.search{position:absolute;top:13px;right:180px;display:flex;align-items:center;gap:6px;font-size:14px;color:#6a5a5c}
.search-field{width:165px;height:24px;background:#9d878b;border:1px solid #7b676a;margin-left:8px}
.search-go{width:28px;height:24px;background:#5fa3d6;color:var(--white);font-size:13px;display:flex;align-items:center;justify-content:center}
.ribbon-end{position:absolute;top:64px;width:86px;height:42px;background:var(--brown);box-shadow:0 2px 4px rgba(0,0,0,.3)}
.ribbon-end.left{left:70px;clip-path:polygon(0 50%,14% 0,100% 0,100% 100%,14% 100%)}
.ribbon-end.right{right:70px;clip-path:polygon(0 0,86% 0,100% 50%,86% 100%,0 100%)}
.nav{position:absolute;left:122px;top:52px;width:956px;height:42px;background:var(--brown);box-shadow:0 3px 5px rgba(0,0,0,.35)}
.nav-inner{position:absolute;left:8px;right:8px;top:5px;bottom:5px;background:var(--brown-mid);border:1px solid #7e5a60}
.nav a{position:absolute;top:9px;font-family:"Fondamento",cursive;color:#f4e6e8;font-size:14px;text-decoration:none;line-height:22px;padding:0 7px}
.nav a.active{background:#3e2024;border-radius:2px}
.hero{position:absolute;left:155px;top:94px;width:890px;height:362px;background:linear-gradient(110deg,#9a9390 0%,#d8d0c6 25%,#c6ad8c 55%,#8a7058 80%,#5b4a40 100%)}
.brand{position:absolute;left:24px;top:250px;display:flex;align-items:center;gap:12px}
.brand-mark{width:34px;height:34px;border-radius:50%;background:#f2a8c4}
.brand-name{font-family:"Nunito Sans",sans-serif;font-weight:600;font-size:34px;color:#5a3a26;line-height:40px}
.hero-caption{position:absolute;right:0;top:209px;width:382px;height:128px;background:rgba(20,20,20,.85);color:var(--white);font-family:"Arimo",sans-serif;font-size:21px;line-height:23px;text-align:right;padding:12px 21px 0 20px}
.welcome{position:absolute;left:178px;top:498px;width:562px}
.welcome h1{font-family:"Fondamento",cursive;font-weight:400;font-size:28px;color:var(--blue-head);margin-bottom:16px;line-height:36px}
.lead-pink{font-size:12px;color:var(--magenta);line-height:18px;letter-spacing:-.1px}
.lead-brown{font-size:12px;color:var(--text-brown);line-height:18px;margin-bottom:8px;letter-spacing:-.1px}
.body-copy{font-size:10.6px;line-height:16px;color:var(--text-brown);padding-left:2px;letter-spacing:-.15px}
.why{position:absolute;left:178px;top:708px;width:560px}
.why h2{font-weight:400;font-size:22px;color:var(--blue-head);margin-bottom:8px}
.why .lead-pink{padding-left:4px}
.cards{position:absolute;left:185px;top:794px;display:flex;gap:6px}
.card{display:flex;width:279px}
.card-photo{width:131px;height:105px;border:1px solid #6a5052;padding:3px;background:var(--white);flex:none}
.card-photo div{width:100%;height:100%}
.card-text{padding-left:6px;font-size:10.6px;line-height:16px;color:var(--text-brown);letter-spacing:-.2px}
.card-text h3{font-weight:400;font-size:11.5px;color:#b3155a;margin-top:2px;white-space:nowrap;letter-spacing:-.2px}
.featured{position:absolute;left:761px;top:492px;width:264px;height:237px;background:var(--feature-pink);border-radius:4px;color:var(--white)}
.panel-title{position:absolute;left:40px;top:26px;font-size:23px;font-weight:400}
.featured-intro{position:absolute;left:40px;top:66px;width:224px;font-size:10.6px;line-height:16px;color:#3a2220;letter-spacing:-.25px}
.featured-photo{position:absolute;left:38px;top:114px;width:96px;height:104px;border-radius:45% 45% 40% 40%;background:radial-gradient(circle at 50% 40%,#b0505f,#6a2a33)}
.featured-list{position:absolute;left:157px;top:109px;width:90px;list-style:none}
.featured-list li{font-size:10.5px;height:22px;line-height:17px;border-bottom:1px dashed rgba(255,255,255,.8);padding-left:2px}
.standard{position:absolute;left:761px;top:733px;width:264px;height:151px;background:var(--standard-blue);border-radius:4px;color:var(--white)}
.standard-photo{position:absolute;left:39px;top:59px;width:90px;height:80px;border:2px solid var(--white);background:linear-gradient(#a59a8e,#d8d2cc)}
.standard-text{position:absolute;left:136px;top:64px;width:124px;font-size:10.8px;line-height:16px;letter-spacing:-.15px}
.standard-text u{display:block;padding-left:4px;font-size:10px;margin-top:2px}
.connect{position:absolute;left:773px;top:903px;display:flex;align-items:center;font-size:10.5px;color:#4a3a3c}
.connect span{margin-right:14px}
.social{width:20px;height:20px;margin-right:7px;border-radius:2px}
.footer-band{position:absolute;left:45px;top:935px;width:1112px;height:65px;background:var(--brown);box-shadow:0 2px 4px rgba(0,0,0,.3)}
.footer{position:absolute;left:146px;top:942px;width:908px;height:65px;background:var(--brown-dark);color:var(--white);text-align:center;font-size:11px}
.footer-links{margin-top:13px}
.footer-links i{font-style:normal;padding:0 5px}
.copyright{margin-top:8px}
</style>
</head>
<body>
<div class="sheet"></div>

<div class="search">Search<div class="search-field"></div><div class="search-go">Go</div></div>

<div class="ribbon-end left"></div>
<div class="ribbon-end right"></div>
<nav class="nav">
  <div class="nav-inner"></div>
  <a style="left:133px">Home</a>
  <a class="active" style="left:225px">About Us</a>
  <a style="left:327px">Photo gallery</a>
  <a style="left:451px">Flavor Menu</a>
  <a style="left:575px">Products</a>
  <a style="left:671px">Contact</a>
  <a style="left:761px">Enquiry</a>
</nav>

<header class="hero" role="img" aria-label="Photo of cupcake toppers, ribbons, pearls, feathers and scissors on a workbench">
  <div class="brand">
    <div class="brand-mark"></div>
    <div class="brand-name">Velvet Ladle Wishes</div>
  </div>
  <div class="hero-caption">At vero eos et accusamus et iusto odio dignissimos ducimus qui blanditiis praesentium voluptatu deleniti atque</div>
</header>

<section class="welcome">
  <h1>Welcome to Velvet Ladle Wishes!</h1>
  <p class="lead-pink">These cases are perfectly simple and easy to distinguish.</p>
  <p class="lead-brown">The wise man therefore always holds in these matters to this principle of selection:</p>
  <p class="body-copy">These cases are perfectly simple and easy to distinguish. In a free hour, when our power of choice is untrammelled and when nothing prevents our being able to do what we like best, every pleasure is to be welcomed and every pain avoided. But in certain circumstances and owing to the claims of duty or the obligations of business it will frequently occur that pleasures have to be repudiated and annoyances accepted. The wise man therefore always holds in these matters to this principle of selection: he rejects pleasures to secure other greater pleasures, or else he endures pains to avoid worse pains</p>
</section>

<section class="why">
  <h2>Why choose us our bakery?</h2>
  <p class="lead-pink">These cases are perfectly simple and easy to distinguish.n a free hour, when our power of choice is untrammelled and when nothing prevents</p>
</section>

<div class="cards">
  <article class="card">
    <div class="card-photo"><div role="img" aria-label="Photo of a pink tiered cupcake stand" style="background:linear-gradient(#e9b0b6,#c84e62)"></div></div>
    <div class="card-text"><h3>At vero eos et accusamus</h3>Temporibus autem quibus-dam et aut officiis debitis aut rerum necessitatibus saepe eveniet ut et voluptates repudiandae .</div>
  </article>
  <article class="card">
    <div class="card-photo"><div role="img" aria-label="Photo of a cupcake with a butterfly topper" style="background:radial-gradient(circle at 50% 55%,#f4efe8 30%,#6b4f36 75%)"></div></div>
    <div class="card-text"><h3>At vero eos et accusamus</h3>Temporibus autem quibus-dam et aut officiis debitis aut rerum necessitatibus saepe eveniet ut et voluptates repudiandae .</div>
  </article>
</div>

<aside class="featured">
  <h2 class="panel-title">Featured Category</h2>
  <p class="featured-intro">The wise man therefore always holds in these matters to this principle of selection:</p>
  <div class="featured-photo" role="img" aria-label="Photo of a chocolate cupcake with sprinkles"></div>
  <ul class="featured-list">
    <li>greater pleasures</li><li>greater pleasures</li><li>greater pleasures</li><li>greater pleasures</li><li>greater pleasures</li>
  </ul>
</aside>

<aside class="standard">
  <h2 class="panel-title">Our Standard</h2>
  <div class="standard-photo" role="img" aria-label="Portrait photo of the head baker"></div>
  <p class="standard-text">The wise man therefore always holds in these matters to this principle <u>more</u></p>
</aside>

<div class="connect">
  <span>Connect with us:</span>
  <div class="social" style="background:#3b5b98"></div>
  <div class="social" style="background:#5fc4ea"></div>
  <div class="social" style="background:#f07a2a"></div>
  <div class="social" style="background:#1c6aa0"></div>
  <div class="social" style="background:#4aa54a"></div>
</div>

<div class="footer-band"></div>
<footer class="footer">
  <div class="footer-links">Home<i>|</i>About Us<i>|</i>Photo gallery<i>|</i>Flavor Menu<i>|</i>Products<i>|</i>Contact<i>|</i>Enquiry</div>
  <div class="copyright">© copyrights velvet ladle wishes.All rights Reserved</div>
</footer>
</body>
</html>
```